Yard sign

Looking for a yard sign. <br/>Something simple, name, number. <br/>Large text, readable from 50 feet away. <br/><br/>18 x 24 inches.

Target Market(s)

Potential homeowners thinking about going solar.

Colors

Designer to choose colors to be used in the design.

Requirements
Must have
• "WE'VE GONE SOLAR!"
Nice to have
• We are a solar company, we would like a design that compliments the homeowners decision that they went solar and encourages others to do the same.

```html
<!DOCTYPE html>
<html lang="en">
<head>
<meta charset="utf-8">
<title>We've Gone Solar – Yard Sign</title>
<link href="https://fonts.googleapis.com/css2?family=Montserrat:wght@700;800;900&display=swap" rel="stylesheet">
<style>
  :root {
    --stage: #606060;
    --sign-orange: #f58e23;
    --sign-white: #ffffff;
    --headline-shadow: rgba(150, 70, 0, 0.75);
    --ink: #231f20;
    --sun-yellow: #fbc12d;
    --pill-orange: #f7941d;
    --pill-yellow: #ffd200;
  }
  * { margin: 0; padding: 0; box-sizing: border-box; }
  html, body {
    width: 1200px;
    height: 955px;
    overflow: hidden;
    background: var(--stage);
  }
  .yard-sign {
    position: absolute;
    left: 107px;
    top: 81px;
    width: 986px;
    height: 737px;
    background: var(--sign-white);
    box-shadow: 0 6px 18px rgba(0, 0, 0, 0.45);
    font-family: "Montserrat", Arial, sans-serif;
  }
  .headline-band {
    position: absolute;
    left: 0; top: 0;
    width: 100%;
    height: 488px;
    background: var(--sign-orange);
  }
  .headline {
    position: absolute;
    left: 0;
    width: 100%;
    text-align: center;
    color: var(--sign-white);
    font-weight: 900;
    line-height: 1;
    text-shadow: 3px 4px 4px var(--headline-shadow);
    white-space: nowrap;
  }
  .headline--top {
    top: 93px;
    font-size: 118px;
    letter-spacing: -0.02em;
    padding-right: 26px;
  }
  .headline--main {
    top: 198px;
    font-size: 222px;
    letter-spacing: -0.03em;
    padding-left: 4px;
  }
  .contact {
    position: absolute;
    left: 74px;
    top: 569px;
  }
  .contact__phone {
    font-size: 46px;
    font-weight: 800;
    color: var(--ink);
    line-height: 1;
    letter-spacing: -0.01em;
    white-space: nowrap;
  }
  .contact__web {
    position: absolute;
    left: -7px;
    top: 74px;
    width: 449px;
    height: 48px;
    border-radius: 24px;
    background: linear-gradient(90deg, var(--pill-orange) 0%, var(--pill-yellow) 50%, var(--pill-orange) 100%);
    color: var(--ink);
    font-size: 33px;
    font-weight: 800;
    line-height: 48px;
    text-align: center;
    letter-spacing: -0.01em;
    white-space: nowrap;
  }
  .brand {
    position: absolute;
    left: 590px;
    top: 575px;
    display: flex;
    align-items: center;
    gap: 18px;
  }
  .brand__mark {
    width: 84px;
    height: 84px;
    border-radius: 50%;
    background: var(--sun-yellow);
    flex-shrink: 0;
  }
  .brand__name {
    color: var(--pill-orange);
    font-weight: 800;
    font-size: 40px;
    line-height: 1.05;
    letter-spacing: -0.01em;
  }
</style>
</head>
<body>
  <main class="yard-sign">
    <section class="headline-band">
      <h1>
        <span class="headline headline--top">WE'VE GONE</span>
        <span class="headline headline--main">SOLAR</span>
      </h1>
    </section>
    <section class="contact">
      <p class="contact__phone">Call us 555-014-2090</p>
      <p class="contact__web">www.brightacresolar.com</p>
    </section>
    <div class="brand">
      <span class="brand__mark"></span>
      <p class="brand__name">Brightacre<br>Solar</p>
    </div>
  </main>
</body>
</html>
```